Cat-products company needs smart, yet endearing, business card

We need a business card design for a new, but up-and-running, business based in Honolulu, Hawaii. The business is Purrnest Nook Co. Our first product is the most environmentally-friendly cat grass kit ever seen on the planet. Future products, currently in the R&D phase, will include a variety of exciting cat scratchers. We also do consulting work to help apartment-dwellers make their home more cat-friendly and, in the future, plan on doing full, custom installs of structure to create high walkways for cats.

Target Market(s)

Middle-aged, apartment-dwelling, middle-class workers who own 1 or more cats and who dote on them.

Industry/Entity Type

Pet Care

Contact Information for Business Card

A striking, professional, yet warm and friendly design is what we're after.

Font styles to use
Serif
Sans Serif
Other font styles liked:
• Comfortaa

Colors

Designer to choose colors to be used in the design.

Requirements
Must have
• The company logo: (see attachment)
• The company name: Purrnest Nook Co
• The web address: www.purrnestnookco.com
• Email: support@purrnestnookco.com
• Phone: +1 (808) 571 6023
• Update (Fri Jun 30 3017 7:45pm Hawaii Time) I would like, is possible, uploaded picture of the cat grass kit on the back of the card with some text along the lines of: Purrnest Nook Co - Maker Of The Leafiest Feline Sprout Set Yet
Nice to have
• A cat picture, cartoon, real or silhouette that illustrates cats in action and/or relaxing; ie using the apartment space to live, play and relax in and being well-contented.
• Most of the website is done in the font: Comfortaa. It might be nice to continue using this for brand consistency.
Should not have
• Hard-to-read fonts.

```html
<!DOCTYPE html>
<html lang="en">
<head>
<meta charset="utf-8">
<title>Purrnest Nook Co – Business Card</title>
<link href="https://fonts.googleapis.com/css2?family=Comfortaa:wght@400;700&display=swap" rel="stylesheet">
<style>
  :root {
    --brown: #5e2f29;
    --brown-light: #7a4238;
    --yellow: #f2c418;
    --white: #ffffff;
    --paper: #f6f6f4;
    --stage: #e8e3dc;
    --text-light: #f4e9e4;
    --photo-top: #f1ede6;
    --photo-mid: #dcc8a6;
    --photo-low: #c99a63;
  }
  * { box-sizing: border-box; margin: 0; padding: 0; }
  html, body {
    width: 1200px; height: 780px; overflow: hidden;
    background: var(--stage);
    font-family: "Comfortaa", sans-serif;
  }
  .stage {
    position: relative; width: 1200px; height: 780px;
    display: flex; align-items: center; justify-content: center; gap: 40px;
  }
  .card {
    position: relative; width: 540px; height: 310px;
    background: var(--white); overflow: hidden;
    box-shadow: 0 10px 28px rgba(60, 35, 20, 0.22);
  }

  /* Front */
  .card-front .wave { position: absolute; inset: 0; }
  .brand {
    position: absolute; display: flex; align-items: center; gap: 12px;
  }
  .brand-mark { width: 22px; height: 22px; background: var(--brown); flex: none; }
  .brand-name {
    font-weight: 700; color: var(--yellow); font-size: 22px; line-height: 1.15;
  }
  .card-front .brand { left: 26px; top: 200px; width: 230px; }
  .person { position: absolute; left: 300px; top: 48px; }
  .person-name {
    color: var(--yellow); font-weight: 700; font-size: 19px; letter-spacing: 0.5px;
  }
  .person-role { color: var(--text-light); font-size: 13px; margin-top: 4px; }
  .contact { position: absolute; left: 318px; top: 170px; list-style: none; }
  .contact li {
    display: flex; align-items: center; gap: 10px;
    color: var(--text-light); font-size: 12px; margin-bottom: 11px;
  }
  .contact-icon {
    width: 18px; height: 18px; background: var(--yellow);
    display: flex; align-items: center; justify-content: center; flex: none;
  }

  /* Back */
  .photo {
    position: absolute; inset: 0 auto 0 0; width: 340px;
    clip-path: polygon(0 0, 100% 0, 78% 100%, 0 100%);
    background: linear-gradient(160deg, var(--photo-top) 0%, var(--photo-mid) 55%, var(--photo-low) 100%);
  }
  .card-back .brand { right: 40px; top: 88px; width: 210px; }
  .socials { position: absolute; right: 92px; top: 196px; display: flex; gap: 16px; }
  .social { width: 20px; height: 20px; background: var(--brown); }
</style>
</head>
<body>
<main class="stage">

  <section class="card card-front" aria-label="Card front">
    <svg class="wave" width="540" height="310" viewBox="0 0 540 310" aria-hidden="true">
      <path d="M232 0 C250 90 330 150 318 310 L540 310 L540 0 Z" fill="var(--brown)"/>
      <path d="M222 0 C240 92 318 152 306 310" fill="none" stroke="var(--yellow)" stroke-width="5"/>
    </svg>

    <div class="brand">
      <span class="brand-mark"></span>
      <span class="brand-name">Purrnest Nook Co</span>
    </div>

    <div class="person">
      <p class="person-name">EMPLOYEE NAME</p>
      <p class="person-role">Manager</p>
    </div>

    <ul class="contact">
      <li>
        <span class="contact-icon">
          <svg width="12" height="12" viewBox="0 0 12 12" aria-hidden="true"><path d="M2.5 1 L4.5 1 L5.2 3.4 L4 4.4 C4.6 5.8 6.2 7.4 7.6 8 L8.6 6.8 L11 7.5 L11 9.5 C11 10.4 10.3 11 9.5 11 C5 11 1 7 1 2.5 C1 1.7 1.6 1 2.5 1 Z" fill="var(--brown)"/></svg>
        </span>+1 (808) 571 6023
      </li>
      <li>
        <span class="contact-icon">
          <svg width="12" height="10" viewBox="0 0 12 10" aria-hidden="true"><rect x="0.5" y="0.5" width="11" height="9" fill="none" stroke="var(--brown)"/><path d="M0.5 0.5 L6 5.5 L11.5 0.5" fill="none" stroke="var(--brown)"/></svg>
        </span>support@purrnestnookco.com
      </li>
      <li>
        <span class="contact-icon">
          <svg width="12" height="12" viewBox="0 0 12 12" aria-hidden="true"><circle cx="6" cy="6" r="5" fill="none" stroke="var(--brown)"/><ellipse cx="6" cy="6" rx="2.2" ry="5" fill="none" stroke="var(--brown)"/><path d="M1 6 H11" stroke="var(--brown)"/></svg>
        </span>www.purrnestnookco.com
      </li>
    </ul>
  </section>

  <section class="card card-back" aria-label="Card back">
    <div class="photo" role="img" aria-label="Photo of two cats leaping between wall-mounted shelves and scratching posts in a bright apartment"></div>

    <div class="brand">
      <span class="brand-mark"></span>
      <span class="brand-name">Purrnest Nook Co</span>
    </div>

    <div class="socials" aria-label="Social channels">
      <span class="social"></span>
      <span class="social"></span>
      <span class="social"></span>
      <span class="social"></span>
    </div>
  </section>

</main>
</body>
</html>
```